I have a logo and need to design the business card and stationery.
Updates

The uploaded logo image named as GREYMARSH CONSTRUCTION which is to be replaced to GREYMARSH CONTRACTS. Kindly add below details and submit the designs- Company name- Greymarsh Engineering Contracts LLP Name & Post- Kelvan Joshi (Designated Partner) Address- Block No.317, Wing C, Tulvo Trade Court, Manek Pural Road, Ruparel Industrial Estate, Goregaon(E), Mumbai - 400 063 Contact- +91 97415 60382 Email- kelvanjoshi@mailbrook.example Website- www.greymarshcontracts.example Contact for Letterhead- +91-22-28754193

Hi Tovin Rahul, We are liking your Design #28860835. We have suggested some changes which are mentioned in feedback. Kindly revert with it asap to finalize this design.

Colors

Designer to choose colors to be used in the design.

```html
<!DOCTYPE html>
<html lang="en">
<head>
<meta charset="utf-8">
<title>Greymarsh Contracts – Business Card</title>
<link rel="stylesheet" href="https://fonts.googleapis.com/css2?family=Michroma&family=Jost:wght@400;600&display=swap">
<style>
  :root {
    --backdrop: #d6d4d1;
    --card-dark: #151515;
    --card-light: #f1f1f0;
    --band-grey: #3d3d3f;
    --ink: #1b1b1b;
    --ink-soft: #444;
    --text-light: #ececec;
    --text-muted: #bdbdbd;
    --block: #1d1d1d;
  }
  * { margin: 0; padding: 0; box-sizing: border-box; }
  html, body { width: 1200px; height: 1014px; overflow: hidden; }
  body {
    background: var(--backdrop);
    font-family: "Jost", sans-serif;
    position: relative;
  }
  .card {
    position: absolute;
    left: 338px;
    width: 524px;
    height: 290px;
    box-shadow: 0 6px 18px rgba(0,0,0,.18);
  }

  /* Back of card */
  .card--back { top: 190px; background: var(--card-dark); }
  .card--back .brand-square {
    position: absolute;
    left: 232px; top: 96px;
    width: 60px; height: 56px;
    background: var(--text-light);
  }
  .card--back .wordmark {
    position: absolute;
    top: 162px; left: 0; right: 0;
    text-align: center;
    font-family: "Michroma", sans-serif;
    color: var(--text-light);
    line-height: 1.15;
  }
  .card--back .wordmark .line-1 { font-size: 20px; letter-spacing: 0.5px; }
  .card--back .wordmark .line-2 { font-size: 10px; letter-spacing: 8.5px; padding-left: 8px; }
  .card--back .web-band {
    position: absolute;
    top: 239px; left: 0; right: 0; height: 32px;
    background: var(--band-grey);
    display: flex; align-items: center; justify-content: center;
    color: var(--text-muted);
    font-size: 12px;
    letter-spacing: 3.4px;
  }

  /* Front of card */
  .card--front { top: 498px; background: var(--card-light); }
  .card--front .mark-block {
    position: absolute;
    left: 87px; top: 53px;
    width: 173px; height: 160px;
    background: var(--block);
  }
  .card--front .wordmark {
    position: absolute;
    left: 271px; top: 50px;
    font-family: "Michroma", sans-serif;
    color: var(--ink);
    line-height: 1.15;
  }
  .card--front .wordmark .line-1 { font-size: 16.5px; }
  .card--front .wordmark .line-2 { font-size: 8.5px; letter-spacing: 5.4px; padding-left: 18px; }
  .person { position: absolute; left: 272px; top: 110px; color: var(--ink); }
  .person .name { font-size: 20px; line-height: 1.1; }
  .person .name strong { font-weight: 600; }
  .person .role { font-size: 12px; color: var(--ink-soft); }
  .contact-list {
    position: absolute; left: 268px; top: 177px;
    list-style: none; font-size: 12.5px; color: var(--ink);
  }
  .contact-list li { display: flex; align-items: center; gap: 7px; height: 19px; }
  .contact-list svg { width: 12px; height: 12px; }
  .address-band {
    position: absolute;
    top: 237px; left: 0; right: 0; height: 33px;
    background: var(--block);
    color: var(--text-muted);
    font-size: 10.5px;
    line-height: 1.4;
    text-align: center;
    padding-top: 3px;
  }
</style>
</head>
<body>
  <section class="card card--back" aria-label="Business card back">
    <div class="brand-square" aria-hidden="true"></div>
    <div class="wordmark">
      <div class="line-1">GREYMARSH</div>
      <div class="line-2">CONTRACTS</div>
    </div>
    <div class="web-band">www.greymarshcontracts.example</div>
  </section>

  <section class="card card--front" aria-label="Business card front">
    <div class="mark-block" aria-hidden="true"></div>
    <div class="wordmark">
      <div class="line-1">GREYMARSH</div>
      <div class="line-2">CONTRACTS</div>
    </div>
    <div class="person">
      <div class="name"><strong>Kelvan</strong> Joshi</div>
      <div class="role">(Designated Partner)</div>
    </div>
    <ul class="contact-list">
      <li>
        <svg viewBox="0 0 12 12" aria-hidden="true"><circle cx="6" cy="6" r="6" fill="#1b1b1b"/><path d="M4 3.2c.3-.2.6-.1.7.2l.4.9c.1.2 0 .4-.2.6l-.3.3c.3.7.9 1.3 1.6 1.6l.3-.3c.2-.2.4-.2.6-.1l.9.4c.3.1.4.4.2.7l-.3.5c-.3.4-.8.5-1.3.3C5.5 7.8 4.2 6.5 3.7 5.1c-.2-.5-.1-1 .3-1.3z" fill="#f1f1f0"/></svg>
        +91 97415 60382
      </li>
      <li>
        <svg viewBox="0 0 12 12" aria-hidden="true"><circle cx="6" cy="6" r="6" fill="#1b1b1b"/><rect x="3" y="4" width="6" height="4.2" fill="#f1f1f0"/><path d="M3 4l3 2.3L9 4" stroke="#1b1b1b" stroke-width=".7" fill="none"/></svg>
        kelvanjoshi@mailbrook.example
      </li>
    </ul>
    <div class="address-band">
      Block No.317, Wing C, Tulvo Trade Court, Manek Pural<br>
      Road, Ruparel Industrial Estate, Goregaon(E), Mumbai - 400 063
    </div>
  </section>
</body>
</html>
```